Event Center Website

We need a new website design for an upscale event center in Reno, Nevada. The building hosts everything from weddings to corporate events to funerals and it competitively more expensive. The overall look and feel is consistent with a Lake Tahoe aesthetic. The current site can be viewed at www.themaplehallevents.com. They are looking for a major upgrade. A sample site they like is www.cliffsidelodgestay.com. We have new photography available (some attached). The site should be very visual. A site map is attached as well for direction on what elements the site should include as well as labels for navigation. I am looking for a home page and sample interior page. Any questions, let me know. Thanks.
Updates

I have added some photography of the center itself for use rather than stock photography. Thanks!

Target Market(s)

Brides, professionals, high-income

Industry/Entity Type

Building

Requirements
Must have
• See site map

```html
<!DOCTYPE html>
<html lang="en">
<head>
<meta charset="utf-8">
<title>Meet Our Team – Maple Hall</title>
<link href="https://fonts.googleapis.com/css2?family=Ubuntu:wght@400;500;700&display=swap" rel="stylesheet">
<style>
:root{
  --brown-dark:#4a2a17;
  --brown:#5a3520;
  --rust:#a9582c;
  --cream:#f5e6c4;
  --cream-soft:#f1e8d8;
  --orange:#d07a1f;
  --amber:#7f4208;
  --contact-bg:#4a2610;
  --contact-rule:#7a4a2a;
  --social-bg:#6a3a18;
  --social-tile:#c9a57a;
  --white:#ffffff;
  --text:#1f1a17;
}
*{box-sizing:border-box;margin:0;padding:0}
html,body{width:1200px;height:945px;overflow:hidden;background:var(--white);font-family:"Ubuntu",sans-serif;color:var(--text)}
.page{position:relative;width:1200px;height:945px}
.hero-banner{position:absolute;left:0;top:0;width:1200px;height:157px;background:linear-gradient(90deg,#3a2412 0%,#c98a2c 22%,#e8b04a 40%,#3a2614 50%,#e3a640 62%,#c07e28 80%,#3a2412 100%)}
.utility-tab{position:absolute;left:849px;top:0;width:227px;height:52px;background:var(--brown-dark);display:flex;align-items:center;justify-content:center}
.utility-tab a{color:var(--white);text-decoration:none;font-size:15px;padding:0 22px}
.utility-tab .divider{width:2px;height:26px;background:var(--white)}
.main-nav{position:absolute;left:100px;top:52px;width:976px;height:58px;background:var(--cream);display:flex;align-items:center}
.brand{display:flex;align-items:center;gap:8px;padding-left:8px;width:205px;font-size:24px;font-weight:500;color:var(--brown-dark)}
.brand .mark{width:14px;height:14px;border-radius:50%;background:var(--brown-dark)}
.main-nav ul{list-style:none;display:flex;gap:34px;margin-left:6px}
.main-nav a{font-size:14.5px;font-weight:500;color:var(--text);text-decoration:none;text-transform:uppercase}
.title-band{position:absolute;left:0;top:157px;width:1200px;height:70px;background:var(--cream-soft);border-bottom:2px solid var(--brown)}
.title-band h1{position:absolute;left:124px;top:20px;font-size:26px;font-weight:500;color:var(--brown-dark);letter-spacing:.3px}
.breadcrumb{position:absolute;right:124px;top:27px;font-size:16px;font-weight:500;color:var(--brown-dark)}
.breadcrumb span{color:var(--rust)}
.section-heading{position:absolute;left:0;top:253px;width:1200px;text-align:center;font-size:34px;font-weight:500;color:var(--brown-dark);letter-spacing:.5px}
.heading-rule{position:absolute;left:563px;top:308px;width:75px;height:2px;background:var(--brown)}
.member-name{position:absolute;left:124px;top:321px;font-size:26px;font-weight:500;color:var(--brown-dark)}
.member-role{position:absolute;left:124px;top:353px;font-size:22px;color:var(--rust)}
.member-rule{position:absolute;left:124px;top:388px;width:952px;height:2px;background:var(--brown)}
.member-photo{position:absolute;left:124px;top:417px;width:382px;height:312px;border:2px solid var(--brown);background:linear-gradient(180deg,#ffffff 0%,#f4ece8 60%,#e9dcd8 100%)}
.member-bio{position:absolute;left:537px;top:416px;width:539px;font-size:13.8px;line-height:25px;text-align:justify;hyphens:auto}
.site-footer{position:absolute;left:0;top:778px;width:1200px;height:167px;background:var(--cream)}
.newsletter{position:absolute;left:131px;top:40px;width:340px;height:60px;background:var(--amber);border-radius:3px;display:flex;overflow:hidden}
.newsletter .field{flex:1;display:flex;align-items:center;justify-content:space-between;padding:0 10px 0 9px;color:var(--white);font-size:14.5px}
.newsletter .send{width:56px;background:var(--orange);color:var(--white);display:flex;align-items:center;justify-content:center;font-size:14.5px}
.contact-box{position:absolute;left:495px;top:41px;width:362px;height:57px;background:var(--contact-bg);border-radius:3px;display:flex;color:var(--white);font-size:12.5px;white-space:nowrap}
.contact-box .address{width:136px;flex:none;border-right:1px solid var(--contact-rule);padding:9px 0 0 10px;line-height:20px}
.contact-box .lines{flex:1;padding:7px 0 0 8px;line-height:22px;font-size:12px}
.contact-box .label{color:var(--orange);margin-right:4px}
.social-box{position:absolute;left:887px;top:41px;width:189px;height:59px;background:var(--social-bg);border-radius:3px;display:flex;align-items:center;justify-content:center;gap:11px}
.social-box span{width:29px;height:29px;background:var(--social-tile);border-radius:2px}
.footer-nav{position:absolute;left:0;top:126px;width:1200px;display:flex;justify-content:center;gap:28px;list-style:none}
.footer-nav a{font-size:14px;color:var(--brown-dark);text-decoration:none;text-transform:uppercase}
</style>
</head>
<body>
<div class="page">
  <div class="hero-banner" role="img" aria-label="Photo of the event hall ceiling with draped fabric and a chandelier"></div>
  <div class="utility-tab"><a href="#">FAQ</a><span class="divider"></span><a href="#">TESTIMONIAL</a></div>
  <nav class="main-nav">
    <div class="brand"><span class="mark"></span>Maple Hall</div>
    <ul>
      <li><a href="#">About Us</a></li>
      <li><a href="#">Gallery</a></li>
      <li><a href="#">Wedding</a></li>
      <li><a href="#">Meetings</a></li>
      <li><a href="#">Other Events</a></li>
      <li><a href="#">Catering</a></li>
      <li><a href="#">Menus</a></li>
    </ul>
  </nav>
  <header class="title-band">
    <h1>MEET OUR TEAM</h1>
    <div class="breadcrumb">HOME / <span>MEET OUR TEAM</span></div>
  </header>
  <h2 class="section-heading">Meet Our Team</h2>
  <div class="heading-rule"></div>
  <h3 class="member-name">Daniel</h3>
  <div class="member-role">Chef</div>
  <div class="member-rule"></div>
  <div class="member-photo" role="img" aria-label="Portrait of the head chef in a light striped shirt, arms crossed"></div>
  <p class="member-bio">Never intending to become a Chef, Daniel began his career at a part-time job in the Pinecrest kitchen. He was immediately drawn in by the excitement of the profession, enjoying the camaraderie, the adrenaline, the rush, the pace, and the noise of the kitchen. From there, Daniel went to work at the Summit Crest Hotel in Lake Tahoe to round out his culinary education. He had the privilege of working with Golden Whisk Award winning chefs, and learned how to execute the finer points of upscale dining. A Reno native, Daniel returned to Northern Nevada bringing his excellent background to Maple Hall. He was recently married to his beautiful wife, Elena.</p>
  <footer class="site-footer">
    <div class="newsletter">
      <div class="field">ENTER YOUR EMAIL
        <svg width="38" height="34" viewBox="0 0 38 34" aria-hidden="true"><path d="M2 14 L19 2 L36 14 V32 H2 Z" fill="#fff" stroke="#7f4208" stroke-width="1.5"/><path d="M2 14 L19 24 L36 14 M2 32 L15 21 M36 32 L23 21" fill="none" stroke="#7f4208" stroke-width="1.5"/><text x="19" y="15" text-anchor="middle" font-size="9" fill="#7f4208" font-family="Ubuntu,sans-serif">@</text></svg>
      </div>
      <div class="send">SEND</div>
    </div>
    <div class="contact-box">
      <div class="address">48 Ridgeview Lane<br>Reno, NV 89511</div>
      <div class="lines"><div><span class="label">Phone:</span> 775-555-0148</div><div><span class="label">Email:</span> info@themaplehallevents.com</div></div>
    </div>
    <div class="social-box"><span></span><span></span><span></span><span></span></div>
    <ul class="footer-nav">
      <li><a href="#">About Us</a></li>
      <li><a href="#">Gallery</a></li>
      <li><a href="#">Wedding</a></li>
      <li><a href="#">Meetings</a></li>
      <li><a href="#">Other Events</a></li>
      <li><a href="#">Catering</a></li>
      <li><a href="#">Menus</a></li>
    </ul>
  </footer>
</div>
</body>
</html>
```